Business card design needed

Business Card design required for new small plumbing business.
Would like a logo/text look that is simple and unique and does not have to be representative of a plumbing company (ie. having a cartoon plumber or toilet etc) as the companyname is self explanatory.
Would like the main colour to be green (lime green).

Industry/Entity Type

Plumber

Contact Information for Business Card

BRAMFORD PLUMBING
ABN 71 546 190 327 004

Simon Harcastle
Licensed Plumber 83615
Phone: 0487 214 670

27 Bramford Drive,
Kelvale. 3958 Tasmania

Email: bramfordplumbing@quellmail.example

Logo Text

Bramford Plumbing

Logo styles of interest
Character Logo
Wordmark Logo
Lettermark Logo

```html
<!DOCTYPE html>
<html lang="en">
<head>
<meta charset="utf-8">
<title>Bramford Plumbing — Business Cards</title>
<link rel="stylesheet" href="https://fonts.googleapis.com/css2?family=Jost:wght@600&family=PT+Sans:wght@400&display=swap">
<style>
  :root {
    --lime: #6aa72e;
    --paper: #ffffff;
    --ink: #161616;
    --stage: #000000;
    --figure-top: #2f4f9a;
    --figure-bottom: #8fb6d8;
  }
  html, body {
    margin: 0;
    width: 1200px;
    height: 849px;
    overflow: hidden;
    background: var(--stage);
  }
  .stage { display: block; width: 1200px; height: 849px; }
  .wordmark {
    font-family: "Jost", "Futura", sans-serif;
    font-weight: 600;
    font-size: 33px;
    letter-spacing: 0.5px;
  }
  .wordmark--dark { fill: var(--ink); }
  .wordmark--light { fill: var(--paper); }
  .holder-name {
    font-family: "PT Sans", "Myriad Pro", sans-serif;
    font-size: 16px;
    fill: var(--lime);
  }
  .detail {
    font-family: "PT Sans", "Myriad Pro", sans-serif;
    font-size: 10px;
    fill: var(--ink);
  }
  .fill-lime { fill: var(--lime); }
  .fill-paper { fill: var(--paper); }
</style>
</head>
<body>
<svg class="stage" viewBox="0 0 1171 828" preserveAspectRatio="none" xmlns="http://www.w3.org/2000/svg">
  <defs>
    <clipPath id="card-shape">
      <rect x="0" y="0" width="455" height="261" rx="12" ry="12"/>
    </clipPath>
    <linearGradient id="mascot-tones" x1="0" y1="0" x2="0" y2="1">
      <stop offset="0" stop-color="var(--figure-top)"/>
      <stop offset="1" stop-color="var(--figure-bottom)"/>
    </linearGradient>
  </defs>

  <!-- Front: white card with contact details -->
  <g class="card card--front" transform="translate(104 283)">
    <g clip-path="url(#card-shape)">
      <rect class="fill-paper" width="455" height="261"/>
      <path class="fill-lime" d="M41 261 V152 A55 55 0 0 1 96 97 H121 V261 Z"/>
      <rect class="fill-lime" x="169" y="97" width="27" height="164"/>
      <rect class="fill-lime" x="169" y="242" width="286" height="19"/>
      <rect x="52" y="115" width="66" height="146" rx="10" fill="url(#mascot-tones)" role="img" aria-label="Cartoon plumber mascot holding a wrench"/>
    </g>
    <text class="wordmark wordmark--dark" x="228" y="50" text-anchor="middle">BRAMFORD PLUMBING</text>
    <text class="holder-name" x="215" y="111">Simon Harcastle</text>
    <text class="detail" x="215" y="127">Licensed Plumber 83615</text>
    <text class="detail" x="218" y="159">BRAMFORD PLUMBING ABN</text>
    <text class="detail" x="218" y="174">71 546 190 327 004</text>
    <text class="detail" x="218" y="188">Phone: 0487 214 670 27</text>
    <text class="detail" x="218" y="203">Bramford Drive, Kelvale. 3958 Tasmania</text>
    <text class="detail" x="218" y="218">Email: bramfordplumbing@quellmail.example</text>
  </g>

  <!-- Back: green card -->
  <g class="card card--back" transform="translate(612 283)">
    <g clip-path="url(#card-shape)">
      <rect class="fill-lime" width="455" height="261"/>
      <path class="fill-paper" d="M38 261 V152 A55 55 0 0 1 93 97 H123 V261 Z"/>
      <rect class="fill-paper" x="169" y="97" width="27" height="164"/>
      <rect class="fill-paper" x="169" y="239" width="286" height="22"/>
      <rect x="52" y="115" width="66" height="146" rx="10" fill="url(#mascot-tones)" role="img" aria-label="Cartoon plumber mascot holding a wrench"/>
    </g>
    <text class="wordmark wordmark--light" x="228" y="50" text-anchor="middle">BRAMFORD PLUMBING</text>
  </g>
</svg>
</body>
</html>
```